Brenwick Structures Construction Company Seeking Modern Website

We are a small construction company wanting to create a web presence. We don't have much in the way of current content but will get photos as they come in. Attached is a picture of our business card.
The pages we would like on the menu are:
Home
Portfolio
Product Specs
Testimonials
Our Process
Contact
Some designs we like are:
http://www.tovasheds-example.com/
http://www.qrnstructures-example.com/
http://dunholtbarns-example.com/
http://pellingframes-example.com/
Not much requirements other than that so feel free to be creative!
Updates
Target Market(s)
Construction
Commercial and Residential Buildings
Industry/Entity Type
Construction Company
Number of Pages Required
5+ page
Look and feel

```html
<!DOCTYPE html>
<html lang="en">
<head>
<meta charset="utf-8">
<title>Brenwick Structures</title>
<link href="https://fonts.googleapis.com/css2?family=Josefin+Slab:wght@400;600;700&family=Open+Sans:ital,wght@0,400;0,600;0,700;1,400&display=swap" rel="stylesheet">
<style>
:root{
  --blue:#13a3e0;
  --blue-dark:#0b8cc4;
  --topbar:#333333;
  --ink:#222222;
  --muted:#777777;
  --red:#e0352b;
  --footer:#2b2b2b;
  --footer-bottom:#1c1c1c;
  --panel:#f5f5f5;
  --wood-a:#3f1f14;
  --wood-b:#6a3522;
  --white:#ffffff;
  --logo:#1e5aa8;
}
*{margin:0;padding:0;box-sizing:border-box}
html,body{width:1200px;height:2632px;overflow:hidden}
body{position:relative;font-family:"Open Sans",Arial,sans-serif;color:var(--ink);
  background:linear-gradient(90deg,var(--wood-a),var(--wood-b) 30%,var(--wood-a) 55%,var(--wood-b) 80%,var(--wood-a))}
.abs{position:absolute}
.slab{font-family:"Josefin Slab",Georgia,serif}

/* top bar */
.topbar{left:0;top:0;width:1200px;height:39px;background:var(--topbar);color:#ddd;font-size:11px}
.topbar .item{position:absolute;top:12px;display:flex;align-items:center;gap:6px}
.topbar .social{position:absolute;right:165px;top:13px;display:flex;gap:18px}
.dot-icon{width:11px;height:11px;border-radius:50%;background:#ddd;display:block}

/* header */
.header{left:0;top:39px;width:1200px;height:73px;background:var(--white)}
.nav{left:0;top:112px;width:1200px;height:42px;background:var(--blue)}
.nav a{position:absolute;top:14px;color:var(--white);font-size:11.5px;text-decoration:none;letter-spacing:.3px}
.logo-bump{left:455px;top:100px;width:290px;height:42px;background:var(--white);border-radius:0 0 50% 50%/0 0 100% 100%}
.logo{left:400px;top:66px;width:400px;text-align:center;font-family:"Josefin Slab",Georgia,serif;font-weight:700;font-size:36px;color:var(--logo)}

/* main column */
.sheet{left:139px;top:154px;width:922px;height:2091px;background:var(--white)}
.hero{left:161px;top:161px;width:877px;height:365px;
  background:linear-gradient(135deg,#a9b7c4,#7f93a6 55%,#96a7b8);
  border-radius:0 0 50% 50%/0 0 34px 34px}
.hero-title{left:161px;top:322px;width:877px;text-align:center;color:var(--white);font-size:35px;letter-spacing:1px}
.hero-dots{left:570px;top:514px;display:flex;gap:5px}
.hero-dots span{width:10px;height:10px;border-radius:50%;background:var(--white)}
.hero-dots span.on{background:var(--red)}

.section-title{width:922px;left:139px;text-align:center;font-size:23px;color:var(--ink)}
.lead{left:205px;width:790px;text-align:center;font-size:10.5px;line-height:18px;color:var(--muted)}
.btn{background:var(--blue);color:var(--white);font-size:11px;text-align:center;font-weight:600}
.divider{left:298px;width:605px;height:1px;background:#e2e2e2}

/* targets */
.target{width:409px;height:244px;box-shadow:0 10px 14px -8px rgba(0,0,0,.45)}
.target .photo{position:absolute;inset:0}
.target .band{position:absolute;left:0;bottom:0;width:100%;height:65px;background:rgba(30,30,30,.78);color:var(--white)}
.target .name{position:absolute;left:14px;top:14px;width:110px;text-align:center;font-size:13.5px;line-height:18px}
.target .desc{position:absolute;left:168px;top:8px;width:230px;font-size:10.5px;line-height:17px}
.target .desc em{font-style:normal;color:var(--red)}

/* portfolio */
.filters{left:139px;top:1306px;width:922px;font-size:11.5px}
.filters span{position:absolute;top:0}
.tile{width:276px;height:192px}
.tile .label{position:absolute;left:0;bottom:0;width:100%;height:47px;background:rgba(19,163,224,.92);color:var(--white);font-size:13px;text-align:center;line-height:47px;letter-spacing:.5px}
.tile .shade{position:absolute;inset:0;background:rgba(20,20,20,.7)}

/* testimonials */
.testi{left:139px;top:1789px;width:922px;height:298px;background:var(--panel)}
.quote{width:320px;font-style:italic;font-size:11px;line-height:20px;color:#444}
.who{font-style:italic;font-weight:700;font-size:11px;color:#333}
.avatar{width:60px;height:60px;border-radius:50%;background:linear-gradient(#cfd6dd,#9aa7b3);border:3px solid var(--white);box-shadow:0 1px 4px rgba(0,0,0,.3)}
.tdots{left:578px;top:2046px;display:flex;gap:6px;align-items:center}
.tdots span{width:11px;height:11px;border-radius:50%;background:var(--blue)}
.tdots span.on{width:16px;height:16px}

/* call to action */
.cta{left:161px;top:2115px;width:877px;height:99px;background:var(--blue);box-shadow:0 12px 14px -10px rgba(0,0,0,.4)}
.cta .l1{position:absolute;left:32px;top:22px;color:var(--white);font-size:17px}
.cta .l2{position:absolute;left:32px;top:51px;color:var(--white);font-size:18px;display:flex;align-items:center;gap:14px}
.cta .quote-btn{position:absolute;left:623px;top:28px;width:202px;height:43px;background:#222;color:var(--white);font-size:13px;text-align:center;line-height:43px}

/* footer */
.footer{left:139px;top:2245px;width:922px;height:202px;background:var(--footer);color:#e8e8e8}
.footer h4{position:absolute;top:24px;font-family:"Josefin Slab",Georgia,serif;font-weight:400;font-size:20px;color:var(--white)}
.footer p,.footer li{font-size:11px;line-height:20px}
.footer ul{list-style:none;position:absolute}
.footer-bottom{left:139px;top:2447px;width:922px;height:39px;background:var(--footer-bottom);color:#ddd;font-size:11px;text-align:center;line-height:39px}
.ghost-name{left:300px;top:2520px;width:600px;text-align:center;font-family:"Josefin Slab",Georgia,serif;font-weight:700;font-size:36px;color:rgba(40,70,110,.45)}
</style>
</head>
<body>

<div class="abs topbar">
  <div class="item" style="left:163px">
    <svg width="11" height="8" viewBox="0 0 11 8"><rect width="11" height="8" fill="#ddd"/><path d="M0 0l5.5 4.5L11 0" stroke="#333" fill="none"/></svg>
    mail@brenwick-example.com
  </div>
  <div class="item" style="left:312px">
    <svg width="10" height="10" viewBox="0 0 24 24"><path fill="#ddd" d="M6.6 10.8a15 15 0 006.6 6.6l2.2-2.2a1 1 0 011-.25 11.4 11.4 0 003.6.57 1 1 0 011 1V20a1 1 0 01-1 1A17 17 0 013 4a1 1 0 011-1h3.5a1 1 0 011 1 11.4 11.4 0 00.57 3.6 1 1 0 01-.25 1z"/></svg>
    - (555) 014-2288.
  </div>
  <div class="social"><i class="dot-icon"></i><i class="dot-icon"></i><i class="dot-icon"></i><i class="dot-icon"></i></div>
</div>

<div class="abs header"></div>
<nav class="abs nav">
  <a style="left:177px">HOME</a>
  <a style="left:251px">PORTFOLIO</a>
  <a style="left:351px">PRODUCT SPECS</a>
  <a style="left:749px">TESTIMONIALS</a>
  <a style="left:868px">OUR PROCESS</a>
  <a style="left:979px">CONTACT</a>
</nav>
<div class="abs logo-bump"></div>
<div class="abs logo">Brenwick Structures</div>

<main>
<div class="abs sheet"></div>

<div class="abs hero" role="img" aria-label="Desk from above with blueprints, calculator, ruler, ear defenders and laptop"></div>
<h1 class="abs hero-title slab" style="font-weight:400">WE BUILD YOUR DREAMS</h1>
<div class="abs hero-dots"><span class="on"></span><span></span><span></span><span></span></div>

<h2 class="abs section-title slab" style="top:589px;font-weight:600">WELCOME TO BRENWICK STRUCTURES.</h2>
<p class="abs lead" style="top:636px">Thomas R. Harlow is a 1972 graduate of the Eastmoor Maritime Academy in Kelston Bay. After a five year stint in the Navy Mr. Harlow attended Ridgefield Law School where he graduated in 1980. He relocated to Corvale, Westland and joined the growing law firm of Ashby and Lorne, where he practiced law for the first few years of his career. Upon leaving AL Mr. Harlow began his own practice and since that time his practice has focused on Civil Litigation. His practice involves a multitude of areas including personal injury, construction and general commercial litigation. He has been lead counsel in numerous state and federal court trials both jury trials and trials to the court.</p>
<div class="abs btn" style="left:542px;top:760px;width:116px;height:33px;line-height:33px">KNOW MORE</div>
<div class="abs divider" style="top:814px"></div>

<h2 class="abs section-title slab" style="top:836px;font-weight:600">OUR TARGETS</h2>
<p class="abs lead" style="top:875px;left:330px;width:540px;line-height:21px">Lorem Ipsum is simply dummy text of the printing and typesetting industry. Lorem Ipsum has been the industry's standard dummy text ever since the 1500s</p>

<div class="abs target" style="left:161px;top:952px">
  <div class="photo" role="img" aria-label="Bright modern office interior with glass walls" style="background:linear-gradient(160deg,#e4eaf2,#9fb3cc 50%,#6d7f96)"></div>
  <div class="band"><div class="name">COMMERCIAL CONSTRUCTION</div><div class="desc">Construction is the process of creating and building infrastructure or a facility and ready for use. <em>More info</em></div></div>
</div>
<div class="abs target" style="left:628px;top:952px">
  <div class="photo" role="img" aria-label="Large two-storey family house lit at dusk" style="background:linear-gradient(170deg,#5d7fc7,#8aa0c8 45%,#6a6b70)"></div>
  <div class="band"><div class="name">RESIDENTIAL BUILDINGS</div><div class="desc">Construction is the process of creating and building infrastructure or a facility and ready for use. <em>More info</em></div></div>
</div>

<div class="abs divider" style="top:1233px"></div>
<h2 class="abs section-title slab" style="top:1253px;font-weight:600">PORTFOLIO</h2>
<div class="abs filters">
  <span style="left:95px;color:var(--red)">Show all</span>
  <span style="left:180px">Education</span>
  <span style="left:272px">Healthcare</span>
  <span style="left:370px">Commercial</span>
  <span style="left:474px">Retail</span>
  <span style="left:544px">Childcare</span>
  <span style="left:634px">Religion</span>
  <span style="left:717px">Government sectors.</span>
</div>

<div class="abs tile" style="left:161px;top:1347px">
  <div class="abs" style="inset:0;background:linear-gradient(135deg,#6b6257,#3c3833)" role="img" aria-label="Living room with sofa and lamp"></div>
  <div class="shade"></div>
  <svg class="abs" style="left:118px;top:84px" width="44" height="22" viewBox="0 0 44 22">
    <circle cx="8" cy="8" r="6" fill="none" stroke="#3aa8e0" stroke-width="2.5"/><path d="M12.5 12.5l5 5" stroke="#3aa8e0" stroke-width="2.5"/>
    <path d="M30 12l6-6M27 8a4 4 0 015-2M39 12a4 4 0 01-5 5" stroke="#3aa8e0" stroke-width="2.5" fill="none"/>
  </svg>
</div>
<div class="abs tile" style="left:461px;top:1347px">
  <div class="abs" style="inset:0;background:linear-gradient(180deg,#4a78c0,#3a3e48 70%)" role="img" aria-label="Modern flat-roof house at night"></div>
  <div class="label">COMMERCIAL &nbsp;INSTALLATION</div>
</div>
<div class="abs tile" style="left:761px;top:1347px">
  <div class="abs" style="inset:0;background:linear-gradient(135deg,#efe0c6,#c79a6a 60%,#9b3a30)" role="img" aria-label="Warm living room with fireplace and red sofas"></div>
  <div class="label">CHILDCARE &nbsp;INSTALLATION</div>
</div>
<div class="abs tile" style="left:161px;top:1566px">
  <div class="abs" style="inset:0;background:linear-gradient(180deg,#bcd9f0,#e8eef3 50%,#7d8a96)" role="img" aria-label="Workers on scaffolding at a white building"></div>
  <div class="label">GOVERNMENT SECTORS</div>
</div>
<div class="abs tile" style="left:461px;top:1566px">
  <div class="abs" style="inset:0;background:linear-gradient(180deg,#5b95cf,#a2633e 45%,#d9cbb6)" role="img" aria-label="House with tiled roof under construction"></div>
  <div class="label">COMMERCIAL &nbsp;INSTALLATION</div>
</div>
<div class="abs tile" style="left:761px;top:1566px">
  <div class="abs" style="inset:0;background:linear-gradient(180deg,#3f8fd6,#d7a66b 50%,#b9884f)" role="img" aria-label="Timber frame of a house under construction"></div>
  <div class="label">RETAIL &nbsp;INSTALLATION</div>
</div>

<section class="abs testi"></section>
<h2 class="abs section-title" style="top:1812px;font-family:'Josefin Slab',Georgia,serif;font-weight:600">TESTIMONIALS</h2>
<p class="abs quote" style="left:181px;top:1874px">" Lorem Ipsum is not simply random text. It has roots in a piece of classical Latin literature from 45 BC, making it over 2000 years old. Edwin Marlowe, a Latin professor at Westbrook College in Dalemoor, looked up one of the more obscure Latin words, consectetur, from a Lorem Ipsum passage "</p>
<div class="abs who" style="left:420px;top:1990px">- Alan Brisco</div>
<div class="abs avatar" style="left:507px;top:1952px" role="img" aria-label="Client portrait"></div>
<p class="abs quote" style="left:635px;top:1874px">" Lorem Ipsum is not simply random text. It has roots in a piece of classical Latin literature from 45 BC, making it over 2000 years old. Edwin Marlowe, a Latin professor at Westbrook College in Dalemoor, looked up one of the more obscure Latin words, consectetur, from a Lorem Ipsum passage "</p>
<div class="abs who" style="left:880px;top:1990px">- Clara Venn</div>
<div class="abs avatar" style="left:961px;top:1952px" role="img" aria-label="Client portrait"></div>
<div class="abs tdots"><span></span><span class="on"></span><span></span></div>

<div class="abs cta">
  <div class="l1 slab">If you need a high quality Constructions for your best buildings</div>
  <div class="l2 slab">JUST CALL US FOR A QUOTE ON 55 014 228 800
    <svg width="16" height="16" viewBox="0 0 24 24"><path fill="#fff" d="M6.6 10.8a15 15 0 006.6 6.6l2.2-2.2a1 1 0 011-.25 11.4 11.4 0 003.6.57 1 1 0 011 1V20a1 1 0 01-1 1A17 17 0 013 4a1 1 0 011-1h3.5a1 1 0 011 1 11.4 11.4 0 00.57 3.6 1 1 0 01-.25 1z"/></svg>
  </div>
  <div class="quote-btn">REQUEST A QUOTE</div>
</div>
</main>

<footer class="abs footer">
  <h4 style="left:24px">OUR PROCESS</h4>
  <p class="abs" style="left:24px;top:58px;width:270px">Lorem Ipsum is simply dummy text of the printing and typesetting industry. Lorem Ipsum has been the industry's standard dummy text ever since...</p>
  <div class="abs btn" style="left:24px;top:128px;width:106px;height:30px;line-height:30px">KNOW MORE</div>

  <h4 style="left:324px">QUICK LINK</h4>
  <ul style="left:324px;top:58px"><li>Home</li><li>Portfolio</li><li>Product Specs</li><li>Testimonials</li><li>Our Process</li><li>Contact</li></ul>

  <h4 style="left:536px">CONTACT US</h4>
  <ul style="left:536px;top:58px">
    <li>18 Aldercrest Road,</li>
    <li>Norvale (QC), H0H 0A0</li>
    <li>Phone &#9990; - (555) 014-2288.</li>
    <li>Email &nbsp;&#9993; - hello@brenwick-example.com</li>
  </ul>

  <h4 style="left:787px">FOLLOW US</h4>
  <div class="abs" style="left:790px;top:62px;display:flex;gap:16px"><i class="dot-icon" style="width:14px;height:14px;background:#fff"></i><i class="dot-icon" style="width:14px;height:14px;background:#fff"></i><i class="dot-icon" style="width:14px;height:14px;background:#fff"></i><i class="dot-icon" style="width:14px;height:14px;background:#fff"></i></div>
</footer>
<div class="abs footer-bottom">© 2015 Brenwick Structures, Inc. All rights reserved.</div>

<div class="abs ghost-name">Brenwick Structures</div>
</body>
</html>
```